Computer consultant business card

Bexil Software is a newly started computer consulting company. It's a small one-man company that provides mostly Vornix applications but also websites in collaboration with designers. I'm running this company on the side of full time university studies.

I want the final design to be clean and memorable. Be creative! :)

Some inspiration:
http://www.pixelmarta.com/design/48317
http://www.pixelmarta.com/design/2739164/business-card-design-by-frostlynk
http://www.pixelmarta.com/design/604281/business-card-design-by-koralind-vestrabanu

See attachment for my company logo.
Updates

I would like to thank everyone for submitting! I'll need a couple of days to review and ultimately select a design.

Target Market(s)

Non-technical entrepreneurs and small companies.

Industry/Entity Type

University

Requirements
Must have
• My company logo.
In any way, both colors from my logo.
First- and last name, e-mail and phone number.
Double-sided design.
Nice to have
• Something creative with the symbol in my logo

```html
<!DOCTYPE html>
<html lang="en">
<head>
<meta charset="utf-8">
<title>Quvro Software – Business Card Sheet</title>
<link rel="stylesheet" href="https://fonts.googleapis.com/css2?family=Nunito+Sans:wght@400;700&family=Questrial&display=swap">
<style>
  :root {
    --sheet-bg: #c4a173;
    --card-white: #ffffff;
    --ink-dark: #2f2e31;
    --brand-blue: #4670bd;
    --accent-teal: #1a8ca6;
    --card-black: #060608;
    --slate-top: #2c2c31;
    --slate-bottom: #4a5a86;
    --label-ink: #1a1a1a;
  }
  * { margin: 0; padding: 0; box-sizing: border-box; }
  html, body { width: 1200px; height: 788px; overflow: hidden; }
  body {
    position: relative;
    background: var(--sheet-bg);
    font-family: "Nunito Sans", Arial, sans-serif;
  }
  .side-label {
    position: absolute;
    width: 524px;
    text-align: center;
    font-size: 20px;
    color: var(--label-ink);
  }
  .card {
    position: absolute;
    width: 524px;
    height: 300px;
    border-radius: 20px;
    overflow: hidden;
    background: var(--card-white);
  }
  .card--front { left: 55px; top: 75px; }
  .card--back-light { left: 622px; top: 75px; }
  .card--back-dark { left: 55px; top: 446px; background: var(--card-black); }
  .card--back-slate {
    left: 622px; top: 446px;
    background: radial-gradient(ellipse 80% 90% at 55% 100%, var(--slate-bottom), var(--slate-top));
  }
  .front-sweep { position: absolute; inset: 0; }
  .holder { position: absolute; left: 34px; top: 37px; color: #fff; }
  .holder__name { font-weight: 700; font-size: 17px; line-height: 1.2; }
  .holder__role { font-size: 12px; opacity: .9; }
  .wordmark {
    position: absolute;
    display: flex;
    align-items: center;
    font-family: "Questrial", "Century Gothic", sans-serif;
    line-height: 1;
  }
  .wordmark__dot { border-radius: 50%; background: var(--brand-blue); flex: none; }
  .wordmark--front { left: 262px; top: 122px; color: var(--ink-dark); font-size: 62px; gap: 16px; }
  .wordmark--front .wordmark__dot { width: 58px; height: 58px; }
  .wordmark--back { left: 0; right: 0; top: 92px; justify-content: center; font-size: 86px; gap: 24px; }
  .wordmark--back .wordmark__dot { width: 100px; height: 100px; }
  .card--back-light .wordmark--back { color: var(--ink-dark); }
  .card--back-dark .wordmark--back,
  .card--back-slate .wordmark--back { color: #fff; }
  .contact {
    position: absolute;
    right: 22px; bottom: 17px;
    display: flex; gap: 16px;
    font-size: 13px;
    color: var(--ink-dark);
  }
  .contact__item { display: flex; align-items: center; gap: 5px; }
  .contact__item svg { width: 9px; height: 9px; }
  .web {
    position: absolute;
    left: 0; right: 0; bottom: 28px;
    text-align: center;
    font-family: "Questrial", "Century Gothic", sans-serif;
    font-size: 19px;
    letter-spacing: 3.5px;
  }
  .card--back-light .web { color: var(--ink-dark); }
  .card--back-dark .web, .card--back-slate .web { color: #fff; }
  .texture {
    position: absolute; inset: 0;
    background:
      radial-gradient(ellipse 30% 40% at 25% 0%, rgba(120,120,125,.55), transparent 70%),
      radial-gradient(ellipse 30% 45% at 78% 100%, rgba(150,140,140,.55), transparent 70%);
  }
</style>
</head>
<body>
  <div class="side-label" style="left:55px; top:34px;">Front</div>
  <div class="side-label" style="left:622px; top:34px;">Back - 1</div>
  <div class="side-label" style="left:55px; top:404px;">Back - 2</div>
  <div class="side-label" style="left:622px; top:404px;">Back - 3</div>

  <section class="card card--front">
    <svg class="front-sweep" viewBox="0 0 524 300" aria-hidden="true">
      <path d="M0 0 H520 C 330 18 150 120 0 282 Z" fill="var(--card-black)"/>
      <path d="M522 2 C 330 22 150 125 2 290" fill="none" stroke="var(--card-white)" stroke-width="8"/>
      <path d="M524 6 C 335 30 160 135 10 302" fill="none" stroke="var(--accent-teal)" stroke-width="9"/>
    </svg>
    <div class="holder">
      <div class="holder__name">Your Name</div>
      <div class="holder__role">Designation</div>
    </div>
    <div class="wordmark wordmark--front"><span class="wordmark__dot"></span><span>quvro</span></div>
    <div class="contact">
      <span class="contact__item">
        <svg viewBox="0 0 10 10"><path d="M2 1 L4 3 L3 4 C4 6 5 7 6 7 L7 6 L9 8 L8 9 C4 9 1 6 1 2 Z" fill="var(--ink-dark)"/></svg>
        +12 345 6789
      </span>
      <span class="contact__item">
        <svg viewBox="0 0 10 10"><rect x="1" y="2.5" width="8" height="5.5" fill="var(--ink-dark)"/><path d="M1 2.5 L5 6 L9 2.5" fill="none" stroke="#fff" stroke-width="1"/></svg>
        info@website.com
      </span>
    </div>
  </section>

  <section class="card card--back-light">
    <div class="wordmark wordmark--back"><span class="wordmark__dot"></span><span>quvro</span></div>
    <div class="web">www.website.com</div>
  </section>

  <section class="card card--back-dark">
    <div class="texture" role="img" aria-label="Perforated metal dot texture in dark grey"></div>
    <div class="wordmark wordmark--back"><span class="wordmark__dot"></span><span>quvro</span></div>
    <div class="web">www.website.com</div>
  </section>

  <section class="card card--back-slate">
    <div class="wordmark wordmark--back"><span class="wordmark__dot"></span><span>quvro</span></div>
    <div class="web">www.website.com</div>
  </section>
</body>
</html>
```